Visitenkarten/Briefpaier/Kassenkassenbelege für Juwelier
Zielgruppe
Mittelständischer Juwelier mit zwei Filialen. Klassischer Schmuck, Uhren und Modeschmuck
Aufgabenstellung
Es müssen für zwei Geschäfte Visitenkarten, Briefpapier (A4) und Kassenkassenbelege (A6) erstellt werden. Logo und Typo im Anhang. Ein Farbkonzept besteht noch nicht. Die Idee geht in Richtung Bordeaux-Rot.
Generell:
(1) Sieht erstmal nach viel Beschreibung aus, bitte nicht entmutigen lassen, sind zu 90% nur austauschbare Inhalts-/Kontaktdaten.
(2) Für meine Zwecke reicht es vollkommen aus, wenn bei den Vorschlägen zur Arbeitsersparnis erstmal nur mit einer Adresse gearbeitet wird. Wenn ich dann den zutreffenden Designvorschlag gefunden habe, können wir die zweite Adresse in dem ersten Format umsetzen. Ich denke das spart Zeit und Nerven.
(3) Bitte Angaben wie "Tel.:" oder "USt.- ID:" nicht wörtlich nehmen, es soll dabei klar sein worum es geht; wenn "Telefon" ausgeschrieben besser aussieht, bitte in der optisch ansprechenderen Form verwenden.
(4) Bei Fragen, bitte fragen!
(5) Viel Spass bei dem Projekt - Ich freu' mich auf die Vorschläge!
Visitenkarten(1):
Juwelier Brenneck GmbH
www.juwelier-brenneck-beispiel.de
Visitenkarten(2):
Visitenkarten(generell):
(1) Die einzelnen Daten können durch Hervorhebungen wie Adresse, Kontakt, Online/Internet unterteilt bzw. hervorgehoben werden.
(2) Die Visitenkarten sollen farbig gedruckt werden; geplant ist weiß als Hintergrund ist aber nicht zwingend bei einer guten anderen Idee
Briefpapier:
(1)Absender im Adressfeld für DIN-lang Briefumschläge mit Fenster:
(2)Informationen im Footer/Seitenbereich:
Juwelier Brenneck Gmb..

```html
<!DOCTYPE html>
<html lang="de">
<head>
<meta charset="utf-8">
<title>Briefpapier Juwelier Brenneck</title>
<link rel="stylesheet" href="https://fonts.googleapis.com/css2?family=Source+Sans+3:wght@400;600;700&display=swap">
<style>
:root{
  --bg:#e6e4e1;
  --paper:#ffffff;
  --ink:#1a1a1a;
  --muted:#9a9a9a;
  --mark:#111111;
  --fold:#d2d2d2;
}
*{margin:0;padding:0;box-sizing:border-box}
html,body{width:1200px;height:979px;overflow:hidden;background:var(--bg)}
body{font-family:"Source Sans 3",sans-serif;color:var(--ink)}
.letter{position:absolute;left:291px;top:42px;width:646px;height:912px;background:var(--paper);box-shadow:0 2px 10px rgba(0,0,0,.12)}
.brand{position:absolute;top:70px;left:0;width:100%;display:flex;justify-content:center;align-items:center;gap:10px}
.brand-dot{width:12px;height:12px;border-radius:50%;background:var(--ink)}
.brand-name{font-size:20px;font-weight:600;color:var(--ink)}
.sender-line{position:absolute;top:154px;left:74px;right:30px;font-size:6.5px;white-space:nowrap;display:flex;justify-content:space-between}
.label{color:var(--muted)}
.recipient{position:absolute;top:179px;left:74px;font-size:10.5px;line-height:13px;font-style:normal}
.recipient strong{font-weight:700}
.recipient .city{margin-top:13px}
.subject{position:absolute;top:305px;left:0;width:100%;text-align:center;font-size:10.5px;font-weight:600;letter-spacing:.3px}
.date{position:absolute;top:325px;right:41px;font-size:10.5px}
.body{position:absolute;top:345px;left:74px;width:532px;font-size:10.5px;line-height:18.5px}
.body p{margin-bottom:18.5px}
.fold{position:absolute;left:0;width:28px;height:1px;background:var(--fold)}
.footer{position:absolute;top:851px;left:0;width:100%;text-align:center;font-size:6.5px;line-height:12.5px}
.footer-mark{position:absolute;bottom:0;left:308px;width:30px;height:13px;background:var(--mark)}
</style>
</head>
<body>
<main class="letter">
  <header class="brand">
    <span class="brand-dot"></span>
    <span class="brand-name">Juwelier Brenneck</span>
  </header>

  <div class="sender-line">
    <span><span class="label">JUWELIER BRENNECK GmbH</span>&nbsp; Goldgasse 12 in 45470 Mülheim a.d. Ruhr</span>
    <span><span class="label">TEL</span> 0208-111222 &nbsp;<span class="label">FAX</span> 0208-111223 &nbsp;<span class="label">info@</span>juwelier-brenneck-beispiel.de &nbsp;<span class="label">www.</span>juwelier-brenneck-beispiel.de</span>
  </div>

  <address class="recipient">
    Frau<br>
    <strong>Henriette Saphir</strong><br>
    Perlenweg 14
    <div class="city">45468 Mülheim an der Ruhr</div>
  </address>

  <span class="fold" style="top:321px"></span>
  <span class="fold" style="top:475px"></span>
  <span class="fold" style="top:639px"></span>

  <h1 class="subject">DIAMANTSTAUB AM HORIZONT</h1>
  <div class="date">Mülheim, den 03. 05. 2014</div>

  <section class="body">
    <p>Sehr geehrte Frau Saphir,</p>
    <p>hier schreibe ich einen Blindtext dahin: Diamanten, die groß genug für die Schmuckproduktion sind, bilden sich nur im Erdmantel unter hohen Drücken und Temperaturen, typischerweise in Tiefen zwischen 150 bis 660 Kilometern[4] und bei Temperaturen von 1200 bis 1400 °C. Diamant-Muttergesteine im Erdmantel sind Peridotit und Eklogit. Letzterer kann versenkte ozeanische Kruste repräsentieren.</p>
    <p>Die jeweilige Transportdauer aus der Tiefe wird auf wenige Stunden geschätzt, sodass aufgrund der Schnelligkeit keine Phasenumwandlung zu Graphit stattfindet. Die letzte Phase der Eruption erfolgt mit Überschallgeschwindigkeit. Diamanten sind Fremd- oder Xenokristalle in Kimberlit und Lamproit und in diesen Magmen chemisch nicht stabil (metastabil).</p>
    <p>So kann man an natürlichen Diamanten immer Auflösungserscheinungen beobachten. Von ihren Vorkommen in Pipes können die Diamantkristalle durch natürliche Verwitterungsprozesse, bei denen sie aufgrund ihrer Härte intakt bleiben, abtransportiert und in Sedimentgesteinen angereichert werden, die heute eine der Hauptquellen dieses Minerals darstellen.</p>
    <p>Mit den allerbesten Grüßen</p>
    <p>Greta Topas</p>
  </section>

  <footer class="footer">
    <div><span class="label">Juwelier Brenneck GmbH</span>&nbsp; Goldgasse 12 in 45470 Mülheim a.d. Ruhr</div>
    <div><span class="label">Geschäftsführer</span> Margarete Brenneck &nbsp;<span class="label">Amtsgericht</span> Musterstadt HRB 00000 &nbsp;<span class="label">Steuernummer</span> 000/0000/0000 &nbsp;<span class="label">USt.-ID</span> DE 000000000</div>
    <div><span class="label">Bank</span> Musterbank AG Essen &nbsp;<span class="label">IBAN</span> DE00 0000 0000 0000 0000 00 &nbsp;<span class="label">BIC</span> MUST DE 0X</div>
  </footer>
  <span class="footer-mark"></span>
</main>
</body>
</html>
```